Real estate broker business card

Want a modern celan but effective business card for my residential and commercial real estate business. I want the back of the card to advertise my services and to capture business. I have attached the back of my current business card fore ideas
Updates

Logos, photo and text updates added! Added Saturday, September 3, 2016

Project Deadline Extended Reason: LOGOS, PHOTOS AND TEST JUST UPLOADED! I'M READY TO PICK A DESIGN! THANK YOU! Added Saturday, September 3, 2016

Target Market(s)

home buyers and seller. commercial buyers and sellers

Industry/Entity Type

Real Estate

Contact Information for Business Card

must have my contact information and my photo

Requirements
Must have
• Carla Ventrino
• Owner & Qualifying Broker
• Ventrino Real Estate Services
• 505.718.2094
• carla@ventrinohomes.example
• www.ventrinohomes.example
Nice to have
• metallic
• Business capture text: " Don't buy or lease property without someone looking out for your best interests. I will represent you on your home or investment purchase for FREE!"
• "Home owners, call today to receive a FREE market analysis for your homes value!

```html
<!DOCTYPE html>
<html lang="en">
<head>
<meta charset="utf-8">
<title>Ventrino Real Estate Services – Business Card</title>
<link rel="stylesheet" href="https://fonts.googleapis.com/css2?family=Source+Sans+3:wght@400;600;700&display=swap">
<style>
  :root {
    --teal: #1a8c9c;
    --teal-dark: #137684;
    --teal-light: #2299a9;
    --silver: #c9cbcd;
    --silver-dark: #8e9193;
    --ink: #4a4d50;
    --white: #ffffff;
    --backdrop: #e9ebec;
  }
  * { margin: 0; padding: 0; box-sizing: border-box; }
  html, body {
    width: 1200px; height: 900px; overflow: hidden;
    background: var(--backdrop);
    font-family: "Source Sans 3", "Helvetica Neue", Arial, sans-serif;
  }
  .card {
    position: absolute;
    overflow: hidden;
    box-shadow: 0 6px 18px rgba(0,0,0,.18);
  }
  .card-shapes { position: absolute; inset: 0; }

  /* Front */
  .card-front { left: 77px; top: 35px; width: 588px; height: 362px; background: var(--white); }
  .brand {
    position: absolute; left: 0; right: 0; top: 88px;
    display: flex; align-items: center; justify-content: center; gap: 14px;
  }
  .brand-mark { width: 22px; height: 22px; background: var(--teal); }
  .brand-name {
    color: var(--teal); font-weight: 600; font-size: 38px; line-height: 1;
    letter-spacing: .5px;
  }
  .brand-sub { display: block; font-size: 19px; letter-spacing: 3px; margin-top: 6px; text-transform: uppercase; }
  .holder {
    position: absolute; right: 307px; top: 264px; text-align: right; color: var(--white);
  }
  .holder-name { font-size: 18px; font-weight: 600; line-height: 22px; }
  .holder-title { font-size: 15.5px; line-height: 22px; }
  .contacts {
    position: absolute; left: 309px; top: 259px; list-style: none; color: var(--white);
    font-size: 15.5px; line-height: 21.5px;
  }
  .contacts li { display: flex; align-items: center; gap: 8px; }
  .contacts svg { width: 11px; height: 11px; fill: var(--white); }

  /* Back */
  .card-back { left: 388px; top: 505px; width: 567px; height: 352px; background: var(--teal); }
  .back-brand {
    position: absolute; left: 0; right: 0; top: 116px; text-align: center;
    color: var(--white); font-weight: 600; font-size: 20px; letter-spacing: 1px;
  }
  .pitch {
    position: absolute; left: 0; right: 0; top: 197px; text-align: center;
    color: var(--white); font-size: 15px; line-height: 20px;
  }
  .pitch p + p { margin-top: 20px; }
</style>
</head>
<body>

<section class="card card-front" aria-label="Card front">
  <svg class="card-shapes" viewBox="0 0 588 362" aria-hidden="true">
    <defs>
      <linearGradient id="silverBar" x1="0" y1="0" x2="0" y2="1">
        <stop offset="0" stop-color="#f4f5f5"/>
        <stop offset=".5" stop-color="var(--silver)"/>
        <stop offset="1" stop-color="var(--silver-dark)"/>
      </linearGradient>
      <linearGradient id="tealBand" x1="0" y1="0" x2="0" y2="1">
        <stop offset="0" stop-color="var(--teal-light)"/>
        <stop offset="1" stop-color="var(--teal-dark)"/>
      </linearGradient>
    </defs>
    <polygon points="0,198 402,198 384,227 0,227" fill="url(#silverBar)"/>
    <polygon points="0,227 384,227 416,190 588,190 588,362 0,362" fill="url(#tealBand)"/>
    <polyline points="0,227 384,227 416,190 588,190" fill="none" stroke="var(--white)" stroke-width="2"/>
  </svg>

  <div class="brand">
    <span class="brand-mark"></span>
    <span class="brand-name">Ventrino<span class="brand-sub">Real Estate Services</span></span>
  </div>

  <div class="holder">
    <div class="holder-name">Carla Ventrino</div>
    <div class="holder-title">Owner &amp; Qualifying Broker</div>
  </div>

  <ul class="contacts">
    <li><svg viewBox="0 0 12 12"><path d="M2 1h2l1 3-1.3 1a6 6 0 0 0 3.3 3.3L8 7l3 1v2a1 1 0 0 1-1 1A9 9 0 0 1 1 2a1 1 0 0 1 1-1z"/></svg>505.718.2094</li>
    <li><svg viewBox="0 0 12 12"><path d="M0 2h12v1.2L6 7 0 3.2z M0 4.6 6 8.4l6-3.8V10H0z"/></svg>carla@ventrinohomes.example</li>
    <li><svg viewBox="0 0 12 12"><circle cx="6" cy="6" r="5.5"/></svg>www.ventrinohomes.example</li>
  </ul>
</section>

<section class="card card-back" aria-label="Card back">
  <svg class="card-shapes" viewBox="0 0 567 352" aria-hidden="true">
    <rect x="0" y="81" width="567" height="94" fill="var(--white)"/>
    <circle cx="282" cy="128" r="95" fill="var(--teal)"/>
  </svg>

  <div class="back-brand">Ventrino</div>

  <div class="pitch">
    <p>Don't buy or lease property without<br>someone looking out for your best interests.<br>I will represent you on your home or investment purchase for FREE!</p>
    <p>Home owners, call today to receive a FREE<br>market analysis for your homes value!</p>
  </div>
</section>

</body>
</html>
```